New Business Card Design for Manufacturing

We are an engineering/manufacturing company that offers Advanced machining/assembly/engineering services, as well as innovative products for the heavy duty engine cooling markets.

We are looking to get a new business card designed that is clean and modern looking, but still fits the wide range of technical/skilled work we do.

- We hope to use this design as the base for other design work in new Presentations, web, and print work.

Industry/Entity Type

Engineering

Contact Information for Business Card

Our preferred color of blue is (RGB) 22/71/159 but can vary slightly from that color. Our content will be our Logo and full company name (Vantrell Forge Works, Inc.), company address, name, job title, phone number with extension, cell number, fax number, website, and email address on the cards.
We'd like the full company name next to the logo, but we are open to other interpretations of that layout.
Preferably, we would like the back side to be clean with just our logo, and the front to contain all of the contact information.

Colors
2f74b4
0355a3
85abd2

Requirements
Must have
• - Logo, company name, needed content - We are open to interpretation beyond that.
• - Standard size business card.
• - Horizontal orientation.
• - Enough space for lengthy names / job titles (for example, a job title could read "Directory of Human Resources" or "V.P. of Governmental Affairs"). We need this to look clean, whether the title be short (CEO) or long (as described above).

```html
<!DOCTYPE html>
<html lang="en">
<head>
<meta charset="utf-8">
<title>Vantrell Forge Works – Business Card</title>
<link href="https://fonts.googleapis.com/css2?family=Crimson+Text&family=Open+Sans:wght@400;700&display=swap" rel="stylesheet">
<style>
  :root {
    --page-bg: #e4e6e8;
    --card-black: #07090b;
    --brand-blue: #0a86c8;
    --band-blue: #0587c9;
    --line-blue: #0d5f9a;
    --ink-white: #ffffff;
  }
  * { box-sizing: border-box; margin: 0; padding: 0; }
  html, body { width: 1200px; height: 1200px; overflow: hidden; background: var(--page-bg); }
  body { position: relative; font-family: "Open Sans", Arial, sans-serif; }

  .card {
    position: absolute;
    left: 200px;
    width: 800px;
    height: 457px;
    background: var(--card-black);
    box-shadow: 0 6px 18px rgba(0,0,0,.25);
    overflow: hidden;
  }
  .card--back { top: 70px; }
  .card--front { top: 620px; }

  .wordmark {
    position: absolute;
    display: flex;
    align-items: center;
    gap: 14px;
    font-family: "Open Sans", Arial, sans-serif;
    font-weight: 700;
    letter-spacing: 1px;
  }
  .wordmark__square { width: 22px; height: 22px; }
  .card--back .wordmark {
    left: 0; right: 0; top: 0; bottom: 0;
    justify-content: center;
    color: var(--ink-white);
    font-size: 58px;
  }
  .card--back .wordmark__square { background: var(--ink-white); width: 30px; height: 30px; }

  .card--front .wordmark {
    left: 0; right: 0; top: 42px;
    justify-content: center;
    color: var(--brand-blue);
    font-size: 50px;
  }
  .card--front .wordmark__square { background: var(--brand-blue); }

  .holder {
    position: absolute;
    top: 128px; left: 0; right: 0;
    text-align: center;
  }
  .holder__line { display: inline-flex; align-items: baseline; gap: 12px; }
  .holder__name {
    font-family: "Crimson Text", Georgia, serif;
    color: var(--brand-blue);
    font-size: 36px;
  }
  .holder__divider { color: var(--brand-blue); font-size: 22px; }
  .holder__title { color: var(--ink-white); font-size: 16px; }
  .holder__phone { color: var(--ink-white); font-size: 16px; margin-top: 2px; }

  .company {
    position: absolute;
    top: 228px; left: 0; right: 0;
    text-align: center;
  }
  .company__name {
    font-family: "Crimson Text", Georgia, serif;
    color: var(--brand-blue);
    font-size: 21px;
    letter-spacing: 1.5px;
    text-transform: uppercase;
  }
  .company__address { color: var(--ink-white); font-size: 16px; margin-top: 2px; }

  .rule {
    position: absolute; left: 0; right: 0;
    height: 1px; background: var(--line-blue);
  }
  .rule--top { top: 304px; }
  .rule--bottom { top: 418px; }

  .contact-band {
    position: absolute;
    top: 312px; left: 0; right: 0; height: 98px;
    background: var(--band-blue);
    display: flex;
    justify-content: center;
    align-items: center;
    color: var(--ink-white);
    font-size: 16px;
  }
  .contact-band__col { display: flex; flex-direction: column; gap: 8px; }
  .contact-band__col--left { align-items: flex-end; padding-right: 16px; }
  .contact-band__col--right { align-items: flex-start; padding-left: 16px; }
  .contact-band__sep { width: 1px; height: 62px; background: rgba(255,255,255,.7); }
  .contact-item { display: flex; align-items: center; gap: 10px; }
  .contact-item__icon {
    width: 18px; height: 18px;
    background: var(--ink-white);
    border-radius: 3px;
    display: flex; align-items: center; justify-content: center;
  }
  .contact-item__icon svg { width: 12px; height: 12px; }
</style>
</head>
<body>

  <section class="card card--back" aria-label="Card back">
    <div class="wordmark"><span class="wordmark__square"></span>Vantrell</div>
  </section>

  <section class="card card--front" aria-label="Card front">
    <div class="wordmark"><span class="wordmark__square"></span>Vantrell</div>

    <div class="holder">
      <div class="holder__line">
        <span class="holder__name">Dara Whitcombe</span>
        <span class="holder__divider">|</span>
        <span class="holder__title">Director</span>
      </div>
      <div class="holder__phone">1 - 555 018275</div>
    </div>

    <div class="company">
      <div class="company__name">Vantrell Forge Works, Inc</div>
      <div class="company__address">Harlow Creek, Ohio, United States</div>
    </div>

    <div class="rule rule--top"></div>
    <div class="contact-band">
      <div class="contact-band__col contact-band__col--left">
        <div class="contact-item">1 - 555-014392 (EXT)
          <span class="contact-item__icon"><svg viewBox="0 0 12 12"><path d="M2 3h8v2H2zM3 6h6v4H3z" fill="#0587c9"/></svg></span>
        </div>
        <div class="contact-item">www.vantrellforge.com
          <span class="contact-item__icon"><svg viewBox="0 0 12 12"><circle cx="6" cy="6" r="4.5" fill="none" stroke="#0587c9" stroke-width="1.4"/><path d="M1.5 6h9M6 1.5v9" stroke="#0587c9" stroke-width="1"/></svg></span>
        </div>
      </div>
      <div class="contact-band__sep"></div>
      <div class="contact-band__col contact-band__col--right">
        <div class="contact-item">
          <span class="contact-item__icon"><svg viewBox="0 0 12 12"><rect x="3.5" y="1" width="5" height="10" rx="1" fill="#0587c9"/></svg></span>1 - 555 016640
        </div>
        <div class="contact-item">
          <span class="contact-item__icon"><svg viewBox="0 0 12 12"><rect x="1" y="3" width="10" height="6.5" fill="none" stroke="#0587c9" stroke-width="1.3"/><path d="M1 3l5 4 5-4" fill="none" stroke="#0587c9" stroke-width="1.3"/></svg></span>dara@vantrellforge.com
        </div>
      </div>
    </div>
    <div class="rule rule--bottom"></div>
  </section>

</body>
</html>
```